Business card design needed

I run a Beautician studio (for 7 years now)
I offer
- Velmo Body Sugaring
- Ruby Glaze
- Nails
- Facials
- Manicure
- Foot Treatment
It might not be necessary to list all those treatments?
Maybe the link to the Website is sufficient?
I leave that up to you ...
(more info on www.FernAndDewByLenka.com.au)
Velmo BodySugaring is our biggest success, It replaces waxing.
I would like to incorporate the logo into the Business Card.
We had many complaints regarding our old Business Cards as the Phone Number was to small.
On the backside, we would like a "your next Appointment" section.
Looking forward to you Design, cheers ... Lenka
Industry/Entity Type
Business
Contact Information for Business Card
Fern by Dew by Lenka
14 Korrin Sqr 3942 Berwick
www.FernAndDewByLenka.com.au
03 9481 2267

```html
<!DOCTYPE html>
<html lang="en">
<head>
<meta charset="utf-8">
<title>Fern &amp; Dew by Lenka – Business Cards</title>
<link href="https://fonts.googleapis.com/css2?family=Ubuntu:wght@300;400;500&family=Open+Sans:ital,wght@0,400;0,600;1,600;1,700&family=Tinos&display=swap" rel="stylesheet">
<style>
  :root {
    --stage: #e9e6e2;
    --card: #ffffff;
    --ink: #2f2f31;
    --ink-soft: #3c3c3e;
    --band-light: #6e6f72;
    --band-dark: #2c2c2e;
    --rule: #6a6a6a;
    --rule-soft: #c9c9c9;
    --brand: #3a3a3a;
    --brand-dot: #f0a21e;
    --faint: rgba(240, 162, 30, 0.10);
  }
  * { box-sizing: border-box; margin: 0; padding: 0; }
  html, body { width: 1200px; height: 788px; overflow: hidden; }
  body {
    position: relative;
    background: var(--stage);
    font-family: "Open Sans", Arial, sans-serif;
    color: var(--ink);
  }
  .side-label {
    position: absolute;
    font-family: "Open Sans", Arial, sans-serif;
    font-size: 20px;
    color: var(--ink);
    transform: translateX(-50%);
  }
  .card {
    position: absolute;
    width: 526px;
    height: 300px;
    background: var(--card);
    border-radius: 22px;
    overflow: hidden;
  }
  .abs { position: absolute; }

  /* Front */
  .card--front { left: 337px; top: 74px; }
  .title-band {
    left: 0; top: 41px; width: 526px; height: 40px;
    display: flex; align-items: center;
  }
  .band { height: 40px; }
  .band--left { width: 41px; flex: none; background: var(--band-light); }
  .band--right { flex: 1; background: var(--band-dark); }
  .front-title {
    flex: none; padding: 0 4px;
    font-family: "Ubuntu", sans-serif; font-weight: 400; font-size: 33px; letter-spacing: 0.3px;
    color: var(--ink-soft); white-space: nowrap; line-height: 40px;
  }
  .contact { left: 33px; top: 214px; font-size: 15.5px; line-height: 22.5px; color: var(--ink); }
  .contact li { list-style: none; display: flex; align-items: center; gap: 7px; }
  .contact svg { width: 12px; height: 12px; fill: var(--ink); flex: none; }

  .brand-mark { text-align: center; font-family: "Ubuntu", sans-serif; font-weight: 500; color: var(--brand); }
  .brand-mark .dot { display: block; margin: 0 auto 8px; border-radius: 50%; background: var(--brand-dot); }
  .brand-mark--front { left: 366px; top: 176px; width: 150px; font-size: 14px; line-height: 18px; }
  .brand-mark--front .dot { width: 70px; height: 70px; }

  /* Back 1 */
  .card--back1 { left: 54px; top: 443px; }
  .back1-title {
    left: 0; top: 12px; width: 526px; text-align: center;
    font-family: "Ubuntu", sans-serif; font-weight: 400; font-size: 25px; letter-spacing: 1px; color: var(--ink-soft);
  }
  .back1-rule { left: 0; top: 51px; width: 526px; height: 1px; background: var(--rule); }
  .faint-disc { left: 165px; top: 60px; width: 210px; height: 210px; border-radius: 50%; background: var(--faint); }
  .heading { font-style: italic; font-weight: 700; font-size: 17px; color: var(--ink); }
  .offer-heading { left: 29px; top: 70px; }
  .offer-list { left: 29px; top: 97px; font-family: "Tinos", serif; font-size: 14.5px; line-height: 20px; color: #444; }
  .offer-list li { list-style: none; }
  .offer-list li::before { content: "▪"; font-size: 9px; margin-right: 6px; vertical-align: 2px; }
  .divider { left: 206px; top: 72px; width: 2px; height: 140px; background: linear-gradient(var(--rule-soft), #555, var(--rule-soft)); }
  .appt-heading { left: 243px; top: 70px; }
  .appt-field { left: 243px; font-size: 16px; display: flex; align-items: flex-end; color: var(--ink); }
  .appt-field .line { border-bottom: 1px solid var(--ink); height: 18px; margin-left: 1px; }
  .hours-heading { left: 0; top: 238px; width: 526px; text-align: center; font-size: 14px; font-style: italic; font-weight: 600; }
  .hours-line { left: 61px; top: 261px; font-size: 12.5px; white-space: nowrap; }
  .hours-line span + span { margin-left: 48px; }

  /* Back 2 */
  .card--back2 { left: 621px; top: 443px; }
  .back2-heading { left: 33px; top: 27px; font-size: 20px; font-style: italic; font-weight: 600; letter-spacing: 1px; }
  .back2-hours { left: 30px; top: 60px; font-size: 17.5px; line-height: 24px; }
  .brand-mark--back { left: 375px; top: 18px; width: 124px; font-size: 12px; line-height: 15px; }
  .brand-mark--back .dot { width: 56px; height: 56px; margin-bottom: 6px; }
  .back2-rule { left: 30px; top: 117px; width: 466px; height: 1px; background: var(--rule-soft); }
  .row { font-size: 18px; display: flex; align-items: flex-end; white-space: nowrap; }
  .row .line { display: inline-block; border-bottom: 1px solid var(--ink); height: 20px; }
  .row--who { left: 46px; top: 143px; }
  .row--date { left: 35px; top: 193px; }
  .row--date .sep { margin: 0 8px; }
  .row--days { left: 60px; top: 248px; gap: 0; align-items: center; font-size: 17px; }
  .box { display: inline-block; width: 22px; height: 22px; border: 1px solid var(--ink); margin-right: 10px; }
  .day { margin-right: 15px; }
</style>
</head>
<body>

<span class="side-label" style="left:600px; top:32px;">Front</span>
<span class="side-label" style="left:323px; top:401px;">Back - 1</span>
<span class="side-label" style="left:897px; top:401px;">Back - 2</span>

<section class="card card--front" aria-label="Front of card">
  <div class="abs title-band">
    <div class="band band--left"></div>
    <h1 class="front-title">FERN&amp;DEW BY LENKA</h1>
    <div class="band band--right"></div>
  </div>
  <ul class="abs contact">
    <li><svg viewBox="0 0 12 12"><path d="M2.5 1.2 4.4 3.4 3.5 4.6c.7 1.5 2 2.8 3.5 3.5l1.2-.9 2.2 1.9-1 1.6C6 10.7 1.3 6 1 2.2z"/></svg>03 9481 2267</li>
    <li><svg viewBox="0 0 12 12"><path d="M6 1 11 6H9.5v5H7V8H5v3H2.5V6H1z"/></svg>14 Korrin Sqr, 3942 Berwick</li>
    <li><svg viewBox="0 0 12 12"><circle cx="6" cy="6" r="4.5"/></svg>www.FernAndDewByLenka.com.au</li>
  </ul>
  <div class="abs brand-mark brand-mark--front"><span class="dot"></span>Velmo Body Sugaring</div>
</section>

<section class="card card--back1" aria-label="Back of card, version one">
  <div class="abs faint-disc"></div>
  <h2 class="abs back1-title">FERN&amp;DEW BY LENKA</h2>
  <div class="abs back1-rule"></div>
  <h3 class="abs heading offer-heading">I offer</h3>
  <ul class="abs offer-list">
    <li>Velmo Body Sugaring</li>
    <li>Ruby Glaze</li>
    <li>Nails</li>
    <li>Facials</li>
    <li>Manicure</li>
    <li>Foot Treatment</li>
  </ul>
  <div class="abs divider"></div>
  <h3 class="abs heading appt-heading">An Appointment</h3>
  <div class="abs appt-field" style="top:110px;">Name<span class="line" style="width:216px;"></span></div>
  <div class="abs appt-field" style="top:150px;">Date<span class="line" style="width:224px;"></span></div>
  <div class="abs appt-field" style="top:190px;">time<span class="line" style="width:160px;"></span>&nbsp;am / pm</div>
  <h4 class="abs hours-heading">Hours of Operation</h4>
  <p class="abs hours-line"><span>Mon. to Fri.&nbsp; 7.30am - 7.00pm</span><span>Sat. 7.30am - 12.00pm</span></p>
</section>

<section class="card card--back2" aria-label="Back of card, version two">
  <h3 class="abs back2-heading">Hours of Operation</h3>
  <p class="abs back2-hours">Monday to Friday -&nbsp; 7.30am - 7.00pm<br>Saturday - 7.30am - 12.00pm</p>
  <div class="abs brand-mark brand-mark--back"><span class="dot"></span>Velmo Body Sugaring</div>
  <div class="abs back2-rule"></div>
  <p class="abs row row--who"><span class="line" style="width:260px;"></span>&nbsp;has an appointment</p>
  <p class="abs row row--date">Date :<span class="line" style="width:42px;"></span><span class="sep">/</span><span class="line" style="width:42px;"></span><span class="sep">/</span><span class="line" style="width:52px;"></span><span class="sep">@</span><span class="line" style="width:42px;"></span><span class="sep">:</span><span class="line" style="width:50px;"></span>am / pm</p>
  <p class="abs row row--days">
    <span class="box"></span><span class="day">Mon.</span>
    <span class="box"></span><span class="day">Tue.</span>
    <span class="box"></span><span class="day">Wed.</span>
    <span class="box"></span><span class="day">Thu.</span>
    <span class="box"></span><span class="day">Fri.</span>
  </p>
</section>

</body>
</html>
```